Clean business card with logo provided

I want a card that will stand out among the masses. I need the color and image to show professionalism and yet have a family appeal showing that I only deal with win/win scenarios. The back of the card will be used to take notes about the individual so I can use that in my database entry. I like modern design but need professionalism in it also. It needs to fit my "clean, safe, and affordable housing" motto. I need to be able to write on the file and update the card details for my employees.

Target Market(s)

Investors looking to make investment income through real estate

Industry/Entity Type

Real Estate

Contact Information for Business Card

Brent Kovalich
blank address, city, st, zip code
480-555-3174
brentkovalich@ridgeworthrentals.example
www.ridgeworthrentals.example

Font styles to use
Sans Serif

Requirements
Must have
• I would like the back of the card to have lines for info. example
• Met/Visited: Date:
• Interets:
Nice to have
• I want the cards color to match the logo background color. Font with details to be san serif and black. I want the card rectangular with square corners. Standard business card size. I would like to see cards designed with both images to see which i prefer more.

```html
<!DOCTYPE html>
<html lang="en">
<head>
<meta charset="utf-8">
<title>Ridgeworth Rentals LLC – Business Card</title>
<link rel="stylesheet" href="https://fonts.googleapis.com/css2?family=Fira+Sans:wght@300;400;600;700&display=swap">
<style>
  :root {
    --teal: #17b4cf;
    --ink: #0b0b0b;
    --paper: #ffffff;
    --stage: #e9e9e7;
    --muted: #dcdcdc;
  }
  * { box-sizing: border-box; margin: 0; padding: 0; }
  html, body { width: 1200px; height: 873px; overflow: hidden; }
  body {
    background: var(--stage);
    font-family: "Fira Sans", sans-serif;
    position: relative;
  }
  .card {
    position: absolute;
    top: 156px;
    width: 330px;
    height: 560px;
    overflow: hidden;
    box-shadow: 0 8px 24px rgba(0,0,0,.18);
  }
  .card-back { left: 225px; background: var(--paper); }
  .card-front { left: 645px; background: var(--ink); }
  .card-shape { position: absolute; inset: 0; width: 100%; height: 100%; }

  .brand { position: absolute; left: 0; right: 0; text-align: center; }
  .brand-name {
    font-weight: 400;
    letter-spacing: .22em;
    text-transform: uppercase;
    line-height: 1.25;
  }
  .brand-tagline { font-weight: 300; margin-top: 6px; }

  .card-front .brand { top: 80px; }
  .card-front .brand-name { color: var(--ink); font-size: 24px; }
  .card-front .brand-tagline { color: var(--ink); font-size: 11px; }

  .card-back .brand { top: 52px; }
  .card-back .brand-name { color: var(--teal); font-size: 17px; }
  .card-back .brand-tagline { color: var(--muted); font-size: 8.5px; }

  .contact {
    position: absolute;
    left: 66px;
    right: 18px;
    top: 340px;
    color: var(--teal);
    font-size: 10px;
    line-height: 1.9;
  }
  .contact-name {
    color: var(--paper);
    font-size: 21px;
    font-weight: 300;
    margin-bottom: 8px;
  }
  .contact-name strong { font-weight: 700; }
  .contact-item { display: flex; align-items: center; gap: 6px; white-space: nowrap; }
  .contact-item svg { width: 10px; height: 10px; flex: none; fill: var(--teal); }
  .website {
    position: absolute;
    left: 24px;
    bottom: 22px;
    color: var(--paper);
    font-size: 11px;
    font-weight: 600;
  }

  .notes {
    position: absolute;
    left: 28px;
    right: 28px;
    top: 270px;
  }
  .note-row {
    display: flex;
    align-items: flex-end;
    height: 50px;
    gap: 8px;
  }
  .note-label {
    color: var(--teal);
    font-weight: 700;
    font-size: 16px;
    white-space: nowrap;
  }
  .note-line { flex: 1; height: 10px; }
  .note-line svg { width: 100%; height: 10px; display: block; }
</style>
</head>
<body>

  <section class="card card-back" aria-label="Card back with note lines">
    <svg class="card-shape" viewBox="0 0 330 560" preserveAspectRatio="none" aria-hidden="true">
      <path d="M0 0 H330 V160 C285 160 260 200 190 208 C110 218 60 215 0 250 Z" fill="var(--ink)"/>
    </svg>
    <div class="brand">
      <div class="brand-name">Ridgeworth<br>Rentals LLC</div>
      <div class="brand-tagline">Providing clean, safe, and affordable housing</div>
    </div>
    <div class="notes">
      <div class="note-row">
        <span class="note-label">Met/Visited:</span>
        <span class="note-line"><svg viewBox="0 0 100 10" preserveAspectRatio="none"><line x1="0" y1="9" x2="100" y2="9" stroke="var(--teal)" stroke-width="1"/></svg></span>
      </div>
      <div class="note-row">
        <span class="note-label">Date:</span>
        <span class="note-line"><svg viewBox="0 0 100 10" preserveAspectRatio="none"><line x1="0" y1="9" x2="100" y2="9" stroke="var(--teal)" stroke-width="1"/></svg></span>
      </div>
      <div class="note-row">
        <span class="note-label">Interets:</span>
        <span class="note-line"><svg viewBox="0 0 100 10" preserveAspectRatio="none"><line x1="0" y1="9" x2="100" y2="9" stroke="var(--teal)" stroke-width="1"/></svg></span>
      </div>
      <div class="note-row">
        <span class="note-line"><svg viewBox="0 0 100 10" preserveAspectRatio="none"><line x1="0" y1="9" x2="100" y2="9" stroke="var(--teal)" stroke-width="1"/></svg></span>
      </div>
      <div class="note-row">
        <span class="note-line"><svg viewBox="0 0 100 10" preserveAspectRatio="none"><line x1="0" y1="9" x2="100" y2="9" stroke="var(--teal)" stroke-width="1"/></svg></span>
      </div>
    </div>
  </section>

  <section class="card card-front" aria-label="Card front with contact details">
    <svg class="card-shape" viewBox="0 0 330 560" preserveAspectRatio="none" aria-hidden="true">
      <path d="M0 0 H330 V235 C300 240 285 275 230 285 C150 298 70 285 0 320 Z" fill="var(--teal)"/>
    </svg>
    <div class="brand">
      <div class="brand-name">Ridgeworth<br>Rentals LLC</div>
      <div class="brand-tagline">Providing clean, safe, and affordable housing</div>
    </div>
    <div class="contact">
      <div class="contact-name"><strong>Brent</strong> Kovalich</div>
      <div class="contact-item">
        <svg viewBox="0 0 10 10" aria-hidden="true"><path d="M5 0 C2.5 0 1 1.8 1 3.8 C1 6.5 5 10 5 10 C5 10 9 6.5 9 3.8 C9 1.8 7.5 0 5 0 Z M5 5.3 A1.5 1.5 0 1 1 5 2.3 A1.5 1.5 0 1 1 5 5.3 Z"/></svg>
        blank address, city, st, zip code
      </div>
      <div class="contact-item">
        <svg viewBox="0 0 10 10" aria-hidden="true"><path d="M2 0.5 L3.8 2.6 L2.8 3.8 C3.5 5.3 4.7 6.5 6.2 7.2 L7.4 6.2 L9.5 8 L8.4 9.5 C4.2 9.3 0.7 5.8 0.5 1.6 Z"/></svg>
        480-555-3174
      </div>
      <div class="contact-item">
        <svg viewBox="0 0 10 10" aria-hidden="true"><path d="M0.5 2 H9.5 V8 H0.5 Z M1 2.5 L5 5.5 L9 2.5" fill="none" stroke="var(--teal)" stroke-width="1"/></svg>
        brentkovalich@ridgeworthrentals.example
      </div>
    </div>
    <div class="website">www.ridgeworthrentals.example</div>
  </section>

</body>
</html>
```